Timber Crest Construction Needs business card

Hey we are in need of business card designs. I have upload our logo as a guideline, but free feel to run with it or come up with something unique.
Pls have fun with it and be creative. the name says it all!
i will give some directions after i see a few entries..
Updates
Logo source file has been uploaded..
Hey because of the logo is so colourful already.
Can we have a few submissions with less colour.
Also we are looking for clever/hidden/descriptive business card.

```html
<!DOCTYPE html>
<html lang="en">
<head>
<meta charset="utf-8">
<title>Timber Crest Construction – Business Card</title>
<link rel="stylesheet" href="https://fonts.googleapis.com/css2?family=Montserrat:wght@400;500;600&display=swap">
<style>
  :root {
    --stage: #2a2a2c;
    --card: #ffffff;
    --ink: #3a3a3d;
    --ink-soft: #6b6b70;
    --band-sky: #bcdcf0;
    --band-slate: #aeb6cc;
    --mark: #7a7a80;
  }
  * { margin: 0; padding: 0; box-sizing: border-box; }
  html, body {
    width: 1200px; height: 864px; overflow: hidden;
    background: var(--stage);
    font-family: "Montserrat", Arial, sans-serif;
    color: var(--ink);
  }
  .stage {
    width: 1200px; height: 864px;
    display: flex; flex-direction: column; align-items: center; justify-content: center;
    gap: 28px;
  }
  .card {
    position: relative;
    width: 700px; height: 400px;
    background: var(--card);
    overflow: hidden;
    box-shadow: 0 10px 30px rgba(0,0,0,.45);
  }

  /* brand lockup */
  .brand {
    display: flex; align-items: center; gap: 14px;
  }
  .brand-square {
    width: 46px; height: 46px; background: var(--mark); flex: none;
  }
  .brand-name {
    font-weight: 500; color: var(--mark);
    line-height: 1.05; letter-spacing: .5px; text-transform: uppercase;
  }

  /* logo face */
  .card--logo .brand {
    position: absolute; left: 50%; top: 110px; transform: translateX(-50%);
  }
  .card--logo .brand-name { font-size: 30px; }
  .web-band {
    position: absolute; left: 0; right: 0; top: 262px; height: 58px;
    background: var(--band-sky);
    display: flex; align-items: center; justify-content: center;
  }
  .web-band span {
    font-size: 17px; letter-spacing: 3px; color: var(--ink);
  }

  /* contact face */
  .card--contact .brand {
    position: absolute; left: 40px; top: 168px;
  }
  .card--contact .brand-square { width: 38px; height: 38px; }
  .card--contact .brand-name { font-size: 24px; }
  .stripe { position: absolute; top: 0; bottom: 0; }
  .stripe--sky { left: 318px; width: 44px; background: var(--band-sky); }
  .stripe--slate { left: 362px; width: 40px; background: var(--band-slate); }

  .details {
    position: absolute; left: 430px; top: 46px; right: 24px;
    font-size: 14px; color: var(--ink);
  }
  .person-name { font-size: 19px; font-weight: 500; letter-spacing: .5px; text-transform: uppercase; }
  .person-role { font-size: 13px; letter-spacing: 1px; text-transform: uppercase; color: var(--ink-soft); margin-top: 2px; }
  .address { margin-top: 46px; line-height: 1.45; font-size: 15px; }
  .contact-list { list-style: none; margin-top: 34px; }
  .contact-list li {
    display: flex; align-items: center; gap: 10px;
    font-size: 13px; line-height: 1; margin-bottom: 11px;
  }
  .contact-list svg { width: 14px; height: 14px; flex: none; fill: var(--ink); }
</style>
</head>
<body>
<main class="stage">

  <section class="card card--logo" aria-label="Business card, brand side">
    <div class="brand">
      <div class="brand-square"></div>
      <div class="brand-name">Timber Crest<br>Construction</div>
    </div>
    <div class="web-band"><span>www.timbercrestbuild.com</span></div>
  </section>

  <section class="card card--contact" aria-label="Business card, contact side">
    <div class="brand">
      <div class="brand-square"></div>
      <div class="brand-name">Timber Crest<br>Construction</div>
    </div>
    <div class="stripe stripe--sky"></div>
    <div class="stripe stripe--slate"></div>

    <div class="details">
      <p class="person-name">Daniel Reeve</p>
      <p class="person-role">General Manager</p>
      <p class="address">42 Larch Road,<br>Mill Yard Street</p>
      <ul class="contact-list">
        <li>
          <svg viewBox="0 0 24 24" aria-hidden="true"><path d="M6.6 10.8a15.1 15.1 0 0 0 6.6 6.6l2.2-2.2c.3-.3.7-.4 1-.2 1.1.4 2.3.6 3.6.6.6 0 1 .4 1 1V20c0 .6-.4 1-1 1A17 17 0 0 1 3 4c0-.6.4-1 1-1h3.5c.6 0 1 .4 1 1 0 1.3.2 2.5.6 3.6.1.3 0 .7-.2 1z"/></svg>
          014 552 3870
        </li>
        <li>
          <svg viewBox="0 0 24 24" aria-hidden="true"><path d="M7 1h10a2 2 0 0 1 2 2v18a2 2 0 0 1-2 2H7a2 2 0 0 1-2-2V3a2 2 0 0 1 2-2zm0 3v14h10V4zm5 15.2a1.2 1.2 0 1 0 0 2.4 1.2 1.2 0 0 0 0-2.4z"/></svg>
          014 552 3871
        </li>
        <li>
          <svg viewBox="0 0 24 24" aria-hidden="true"><path d="M2 5h20v14H2zm2 2v.4l8 5 8-5V7zm0 2.8V17h16V9.8l-8 5z"/></svg>
          hello@timbercrest.com
        </li>
        <li>
          <svg viewBox="0 0 24 24" aria-hidden="true"><path d="M12 2a10 10 0 1 0 0 20 10 10 0 0 0 0-20zm6.9 6h-3a15 15 0 0 0-1.3-3.9A8 8 0 0 1 18.9 8zM12 4c.8 1.2 1.5 2.5 1.9 4h-3.8c.4-1.5 1.1-2.8 1.9-4zM4.3 14a8 8 0 0 1 0-4h3.4a16 16 0 0 0 0 4zm.8 2h3a15 15 0 0 0 1.3 3.9A8 8 0 0 1 5.1 16zm3-8h-3a8 8 0 0 1 4.3-3.9C8.9 5.3 8.4 6.6 8.1 8zM12 20c-.8-1.2-1.5-2.5-1.9-4h3.8c-.4 1.5-1.1 2.8-1.9 4zm2.3-6H9.7a14 14 0 0 1 0-4h4.6a14 14 0 0 1 0 4zm.3 5.9c.6-1.2 1-2.5 1.3-3.9h3a8 8 0 0 1-4.3 3.9zm1.7-5.9a16 16 0 0 0 0-4h3.4a8 8 0 0 1 0 4z"/></svg>
          www.timbercrestbuild.com
        </li>
      </ul>
    </div>
  </section>

</main>
</body>
</html>
```